Party Favors and Decorations Business Needs A Business Card Design

We are in need of a Logo design and business card design for a new small business called Bright Lantern Designs. We create party decorations and favours for Bridal Showers, Baby Showers, Weddings Birthdays etc. This is a very personalized service based on Clients theme, colour, and style. We are looking for a high end elegant look. I have attached a file to the style I like including the type of paper.

Target Market(s)

women, young adults, expectant mothers, mothers

Industry/Entity Type

Small Business

Contact Information for Business Card

Bright Lantern Designs Essex, ON 519-847-2061 brightlanterndesigns.ca karen@brightlanterngiftbox.com find us on Chatterly

Logo Text

Bright Lantern Designs

Font styles to use
Script

Requirements
Must have
• Name, email, web address, phone number
Should not have
• cutesy graphics

```html
<!DOCTYPE html>
<html lang="en">
<head>
<meta charset="utf-8">
<title>Bright Lantern Designs – Business Card</title>
<link rel="stylesheet" href="https://fonts.googleapis.com/css2?family=Lora:wght@400&family=Arimo:wght@400;700&family=Courgette&display=swap">
<style>
  :root {
    --ink: #0d0d0d;
    --paper: #f4f4f4;
    --paper-shade: #e2e2e2;
    --slate: #8e8e8e;
    --slate-dark: #5f5f5f;
    --stage: #d9d6d1;
  }
  * { margin: 0; padding: 0; box-sizing: border-box; }
  html, body { width: 1200px; height: 902px; overflow: hidden; }
  body { background: var(--stage); position: relative; font-family: "Arimo", Arial, sans-serif; }

  .card {
    position: absolute;
    width: 540px;
    height: 309px;
    box-shadow: 0 14px 30px rgba(0,0,0,0.28);
    overflow: hidden;
  }
  .card svg.card-art { position: absolute; inset: 0; width: 100%; height: 100%; }

  .card--front { left: 60px; top: 110px; }
  .card--back  { left: 600px; top: 480px; }

  .wordmark {
    position: absolute;
    font-family: "Lora", Georgia, serif;
    font-weight: 400;
    line-height: 1.05;
    text-align: center;
  }
  .card--front .wordmark {
    left: 0; right: 0; top: 96px;
    font-size: 46px; color: var(--ink);
  }
  .wordmark .wordmark-line { display: block; }
  .wordmark .wordmark-line--small { font-size: 0.6em; margin-top: 4px; }

  .social {
    position: absolute; left: 44px; bottom: 34px;
    display: flex; align-items: center; gap: 8px;
    color: var(--ink);
  }
  .social-square { width: 20px; height: 20px; background: var(--ink); }
  .social-text { line-height: 1; }
  .social-lead { display: block; font-size: 9px; }
  .social-name { display: block; font-size: 15px; }

  .card--back .wordmark {
    left: 40px; top: 118px; width: 280px;
    font-size: 34px; color: var(--paper);
  }

  .person { position: absolute; right: 62px; top: 66px; text-align: right; color: var(--paper); }
  .person-name { font-family: "Courgette", cursive; font-size: 26px; display: block; }
  .person-role { font-size: 12px; display: block; margin-top: 2px; }

  .contact {
    position: absolute; left: 46px; bottom: 40px;
    list-style: none; color: var(--paper); font-size: 14px;
  }
  .contact li { display: flex; align-items: center; gap: 10px; margin-top: 7px; }
  .contact svg { width: 14px; height: 14px; flex: none; fill: var(--paper); }
</style>
</head>
<body>

<section class="card card--front" aria-label="Card front">
  <svg class="card-art" viewBox="0 0 540 309" preserveAspectRatio="none" aria-hidden="true">
    <rect width="540" height="309" fill="var(--ink)"/>
    <polygon points="22,28 455,28 518,112 518,248 340,248 300,286 22,286" fill="var(--paper)"/>
    <polygon points="400,0 540,0 540,110" fill="var(--slate)"/>
    <polygon points="0,190 150,236 270,236 300,286 0,309" fill="var(--slate)"/>
    <polygon points="22,232 150,262 290,262 300,286 22,286" fill="var(--paper-shade)"/>
  </svg>
  <div class="wordmark">
    <span class="wordmark-line">Bright Lantern</span>
    <span class="wordmark-line wordmark-line--small">Designs</span>
  </div>
  <div class="social">
    <span class="social-square"></span>
    <span class="social-text">
      <span class="social-lead">Find us on</span>
      <span class="social-name">Chatterly</span>
    </span>
  </div>
</section>

<section class="card card--back" aria-label="Card back">
  <svg class="card-art" viewBox="0 0 540 309" preserveAspectRatio="none" aria-hidden="true">
    <rect width="540" height="309" fill="var(--paper)"/>
    <rect x="24" y="22" width="492" height="265" fill="var(--ink)"/>
    <polygon points="24,22 190,22 150,110 24,110" fill="var(--paper)"/>
    <polygon points="470,22 540,22 540,309 516,309 516,190" fill="var(--slate)"/>
    <polygon points="24,110 150,110 24,160" fill="var(--slate-dark)" opacity="0.35"/>
  </svg>
  <div class="wordmark">
    <span class="wordmark-line">Bright Lantern</span>
    <span class="wordmark-line wordmark-line--small">Designs</span>
  </div>
  <div class="person">
    <span class="person-name">Employee name</span>
    <span class="person-role">Managing Director</span>
  </div>
  <ul class="contact">
    <li>
      <svg viewBox="0 0 24 24" aria-hidden="true"><path d="M6.6 10.8a15 15 0 0 0 6.6 6.6l2.2-2.2c.3-.3.7-.4 1-.2 1.1.4 2.3.6 3.6.6.6 0 1 .4 1 1V20c0 .6-.4 1-1 1A17 17 0 0 1 3 4c0-.6.4-1 1-1h3.5c.6 0 1 .4 1 1 0 1.3.2 2.5.6 3.6.1.3 0 .7-.2 1z"/></svg>
      519-847-2061
    </li>
    <li>
      <svg viewBox="0 0 24 24" aria-hidden="true"><circle cx="12" cy="12" r="10"/></svg>
      www.brightlanterndesigns.ca
    </li>
    <li>
      <svg viewBox="0 0 24 24" aria-hidden="true"><path d="M2 5h20v14H2z M2 5l10 8 10-8" fill="none" stroke="#f4f4f4" stroke-width="2"/></svg>
      karen@brightlanterngiftbox.com
    </li>
  </ul>
</section>

</body>
</html>
```